Business card por a urban DJ, up scale audience target

Need a sober design, modern, conservative colors but i can consider some options, y play rnb, hip hop, EDM and top40.

Business card for contact and personal info, double sided, use logo attrached please; im 42 so i need a card acording to my age an target audience.

Target Market(s)

Adult people, up scale audience

Industry/Entity Type

Music Download

Contact Information for Business Card

Cel (318) 4207265518 www.lumadrift.com

Requirements
Must have
• open mind
Nice to have
• open mind
Should not have
• DJ

```html
<!DOCTYPE html>
<html lang="en">
<head>
<meta charset="utf-8">
<title>Luma — Business Card</title>
<link href="https://fonts.googleapis.com/css2?family=Open+Sans:wght@600;800&display=swap" rel="stylesheet">
<style>
  :root {
    --backdrop: #e9ecec;
    --ink: #151515;
    --card-black: #0e0e0e;
    --card-black-light: #262626;
    --card-white: #f4f4f4;
    --band-dark: #1c1c1c;
    --band-light: #3a3a3a;
    --paper-text: #1a1a1a;
    --white: #ffffff;
  }
  html, body {
    margin: 0;
    padding: 0;
    width: 1200px;
    height: 900px;
    overflow: hidden;
    background: var(--backdrop);
    font-family: "Open Sans", Arial, sans-serif;
  }
  .sheet {
    width: 1200px;
    height: 900px;
    display: flex;
    flex-direction: column;
    align-items: center;
    justify-content: center;
    gap: 56px;
  }
  .card {
    position: relative;
    width: 660px;
    height: 378px;
    box-shadow: 0 6px 18px rgba(0,0,0,0.18);
    overflow: hidden;
  }
  .card-front {
    background: radial-gradient(ellipse at 50% 40%, var(--card-black-light) 0%, var(--card-black) 75%);
    display: flex;
    align-items: center;
    justify-content: center;
  }
  .brand-name {
    font-weight: 800;
    letter-spacing: 4px;
    line-height: 1;
    margin: 0;
  }
  .card-front .brand-name {
    color: var(--white);
    font-size: 92px;
  }
  .card-back {
    background: var(--card-white);
  }
  .back-content {
    position: absolute;
    left: 0;
    top: 0;
    right: 0;
    bottom: 54px;
    display: flex;
    align-items: center;
  }
  .card-back .brand-name {
    color: var(--paper-text);
    font-size: 68px;
    width: 300px;
    text-align: center;
    margin-left: 40px;
  }
  .divider {
    width: 2px;
    height: 150px;
    background: var(--paper-text);
    margin: 0 36px 0 28px;
  }
  .contact-list {
    list-style: none;
    margin: 0;
    padding: 0;
    display: flex;
    flex-direction: column;
    gap: 14px;
  }
  .contact-item {
    display: flex;
    align-items: center;
    gap: 12px;
    font-weight: 600;
    font-size: 17px;
    color: var(--paper-text);
  }
  .contact-icon {
    width: 18px;
    height: 18px;
    flex: none;
  }
  .edge-band {
    position: absolute;
    left: 0;
    right: 0;
    bottom: 0;
    height: 54px;
    background: linear-gradient(180deg, var(--band-light) 0%, var(--band-dark) 100%);
  }
</style>
</head>
<body>
  <main class="sheet">
    <section class="card card-front" aria-label="Card front">
      <p class="brand-name">LUMA</p>
    </section>

    <section class="card card-back" aria-label="Card back">
      <div class="back-content">
        <p class="brand-name">LUMA</p>
        <div class="divider"></div>
        <ul class="contact-list">
          <li class="contact-item">
            <svg class="contact-icon" viewBox="0 0 18 18" aria-hidden="true">
              <rect x="5" y="1.5" width="8" height="15" rx="1.5" fill="none" stroke="#1a1a1a" stroke-width="1.4"/>
              <line x1="8" y1="14" x2="10" y2="14" stroke="#1a1a1a" stroke-width="1.2"/>
            </svg>
            <span>(318) 4207265518</span>
          </li>
          <li class="contact-item">
            <svg class="contact-icon" viewBox="0 0 18 18" aria-hidden="true">
              <circle cx="9" cy="9" r="8" fill="#1a1a1a"/>
              <ellipse cx="9" cy="9" rx="3.4" ry="8" fill="none" stroke="#f4f4f4" stroke-width="1"/>
              <line x1="1" y1="9" x2="17" y2="9" stroke="#f4f4f4" stroke-width="1"/>
              <line x1="2.6" y1="5" x2="15.4" y2="5" stroke="#f4f4f4" stroke-width="0.9"/>
              <line x1="2.6" y1="13" x2="15.4" y2="13" stroke="#f4f4f4" stroke-width="0.9"/>
            </svg>
            <span>www.lumadrift.com</span>
          </li>
        </ul>
      </div>
      <div class="edge-band" role="img" aria-label="Dark carbon-texture band"></div>
    </section>
  </main>
</body>
</html>
```